Business Cards - Brightpath Horizon

need to design unique business card for my mortgage business. I need to design credit card style business card for my business or any unique idea that you might have

Target Market(s)

Home Loan customers

Industry/Entity Type

Mortgage Brokerage

Contact Information for Business Card

please design credit card style or very unique style business card

Colors

Designer to choose colors to be used in the design.

Requirements
Must have
• Name
• position
• Phone number
• fax number
• email address
• website address
• social media address
• All above fields will be provided once design in finalised

```html
<!DOCTYPE html>
<html lang="en">
<head>
<meta charset="utf-8">
<title>Brightpath Horizon – Business Cards</title>
<link href="https://fonts.googleapis.com/css2?family=Roboto:wght@400;500;700&display=swap" rel="stylesheet">
<style>
  :root {
    --stage: #232323;
    --brand-blue: #0a36c9;
    --tree-blue: #2a51d2;
    --paper: #f2f2f2;
    --accent-orange: #f7891c;
    --ink-grey: #555555;
    --white: #ffffff;
  }
  * { margin: 0; padding: 0; box-sizing: border-box; }
  html, body {
    width: 1200px; height: 960px; overflow: hidden;
    background: var(--stage);
    font-family: "Roboto", Arial, sans-serif;
  }
  .canvas { position: relative; width: 1200px; height: 960px; }

  .card {
    position: absolute; left: 320px; width: 600px; height: 342px;
    border-radius: 18px; overflow: hidden;
  }
  .card--front { top: 106px; background: var(--brand-blue); }
  .card--back { top: 493px; background: var(--paper); }

  .front__tree {
    position: absolute; left: 84px; top: 12px; width: 434px; height: 290px;
    border-radius: 50% 50% 44% 44%;
    background: radial-gradient(ellipse at center, var(--tree-blue) 0%, rgba(42,81,210,0.55) 60%, rgba(42,81,210,0) 100%);
  }
  .front__brand {
    position: absolute; left: 0; right: 0; top: 118px;
    text-align: center; color: var(--white);
    font-weight: 500; font-size: 46px; line-height: 54px;
    text-transform: uppercase; letter-spacing: 2px;
  }
  .front__social { position: absolute; left: 0; top: 284px; }

  .back__brand {
    position: absolute; right: 38px; top: 62px; width: 250px;
    text-align: center; color: var(--brand-blue);
    font-weight: 500; font-size: 30px; line-height: 34px;
    text-transform: uppercase; letter-spacing: 1px;
  }
  .back__tagline {
    position: absolute; right: 36px; top: 148px; width: 250px;
    text-align: center; color: var(--accent-orange);
    font-size: 15px; line-height: 18px;
  }
  .contact { position: absolute; left: 34px; top: 136px; }
  .contact__name { color: var(--brand-blue); font-size: 20px; font-weight: 500; line-height: 24px; }
  .contact__role { color: var(--accent-orange); font-size: 15px; font-weight: 500; line-height: 20px; margin-bottom: 10px; }
  .contact__address { color: var(--ink-grey); font-size: 15px; line-height: 18px; margin-bottom: 11px; }
  .contact__list { list-style: none; }
  .contact__item {
    display: flex; align-items: center; gap: 9px;
    color: var(--ink-grey); font-size: 15px; line-height: 19px;
  }
  .contact__icon { width: 14px; height: 14px; flex: none; }
</style>
</head>
<body>
<div class="canvas">

  <section class="card card--front">
    <div class="front__tree" role="img" aria-label="Faint tree illustration behind the company name"></div>
    <div class="front__brand">Brightpath<br>Horizon</div>
    <svg class="front__social" width="600" height="40" viewBox="0 0 600 40" aria-label="Social media links">
      <line x1="63" y1="20" x2="240" y2="20" stroke="var(--white)" stroke-width="1.5"/>
      <line x1="364" y1="20" x2="542" y2="20" stroke="var(--white)" stroke-width="1.5"/>
      <circle cx="252" cy="20" r="14" fill="var(--white)"/>
      <circle cx="284" cy="20" r="14" fill="var(--white)"/>
      <circle cx="318" cy="20" r="14" fill="var(--white)"/>
      <circle cx="351" cy="20" r="14" fill="var(--white)"/>
    </svg>
  </section>

  <section class="card card--back">
    <div class="back__brand">Brightpath<br>Horizon</div>
    <div class="back__tagline">Sound choice, Steady home</div>

    <div class="contact">
      <div class="contact__name">DANIEL REYES</div>
      <div class="contact__role">CEO/FOUNDER</div>
      <div class="contact__address">2140 Willow Bend Road<br>Juneau, Alaska 99801</div>
      <ul class="contact__list">
        <li class="contact__item">
          <svg class="contact__icon" viewBox="0 0 14 14"><path d="M3 1l2.5 2.6-1.3 1.6c.8 1.8 2.2 3.2 4 4l1.6-1.3L12.4 10.4 11 13C5.7 12.6 1.4 8.3 1 3z" fill="var(--brand-blue)"/></svg>
          555 210 4836
        </li>
        <li class="contact__item">
          <svg class="contact__icon" viewBox="0 0 14 14"><rect x="3.5" y="1" width="7" height="4" fill="var(--brand-blue)"/><rect x="1" y="5.5" width="12" height="5" rx="1" fill="var(--brand-blue)"/><rect x="3.5" y="9" width="7" height="4" fill="var(--brand-blue)"/></svg>
          555 210 4837
        </li>
        <li class="contact__item">
          <svg class="contact__icon" viewBox="0 0 14 14"><rect x="1" y="3" width="12" height="8.5" fill="var(--brand-blue)"/><path d="M1.5 3.5L7 8l5.5-4.5" stroke="var(--paper)" stroke-width="1.2" fill="none"/></svg>
          mail@brightpath.com
        </li>
        <li class="contact__item">
          <svg class="contact__icon" viewBox="0 0 14 14"><circle cx="7" cy="7" r="6" fill="var(--brand-blue)"/><path d="M1 7h12M7 1c-2.5 3-2.5 9 0 12M7 1c2.5 3 2.5 9 0 12" stroke="var(--paper)" stroke-width="0.9" fill="none"/></svg>
          www.brightpath.com
        </li>
      </ul>
    </div>
  </section>

</div>
</body>
</html>
```